Sleep/Snoring Business - Requires Website - Australia

We are seeking a simple to maintain website for our sleep business. The health care business provides diagnostic and treatment solutions for snoring, sleep disorders and other respiratory problems.

Ideally, colours to match the company logo (attached).

The page must be built using WORDPRESS.

Ideally site will have a home page outlining the business, with 5 sub pages - being "Diagnosis" "Treatment Options", "Prodcuts", "About Us", "Contact Us"

The site home page should include a large picture on the home page.

The "Treatment Options" and "Diagnosis" pages must include:
Allow for a few pictures with assocaited text, plus space for some embeded youtube videos.

"Prodcuts" page should have the ability to show 3-4 products across the page with text below.. that can include external URL to products

The "About Us" page must include:
1. a Map (google map) to identify the various locations. There are 6 in total.
2. A Section to describe our doctors/staff - allow for a picture and some text

The "Contact Us" page must include:
email form
telephone details

The overall design should have a clean and medical/safe feeling

Target Market(s)

People who snore and those with sleeping and respiratory disorders

Industry/Entity Type

Health Care

Coding

Coded - Design and coding required

Number of Pages Required

5+ page

Colors

Designer to choose colors to be used in the design.

Requirements
Must have
• The page must be built using WORDPRESS.
• Ideally site will have a home page outlining the business, with 5 sub pages - being "Diagnosis" "Treatment Options", "Prodcuts", "About Us", "Contact Us"
• The site home page should include a large picture on the home page.
• The "Treatment Options" and "Diagnosis" pages must include:
• Allow for a few pictures with assocaited text, plus space for some embeded youtube videos.
• "Prodcuts" page should have the ability to show 3-4 products across the page with text below.. that can include external URL to products
• The "About Us" page must include:
• 1. a Map (google map) to identify the various locations. There are 6 in total.
• 2. A Section to describe our doctors/staff - allow for a picture and some text
• The "Contact Us" page must include:
• email form
• telephone details
• Pictures must be licenced or free to use
Nice to have
• Home page pictures showing people sleeping well, snoring or fresh air (landscape) type transition pictures (at least 3).
Should not have
• Not to look cheap
• This is a high end healthcare business, so must look that way

```html
<!DOCTYPE html>
<html lang="en">
<head>
<meta charset="utf-8">
<title>Restwell Clinic – Home</title>
<link rel="stylesheet" href="https://fonts.googleapis.com/css2?family=Lato:wght@400;700&family=Cabin:wght@500&display=swap">
<style>
  :root{
    --navy:#0f4c7d;
    --sky:#8eaed6;
    --sky-soft:#e3ebf6;
    --ink:#333333;
    --rule:#d4d9de;
    --white:#ffffff;
    --dot:#8c8c8c;
  }
  *{margin:0;padding:0;box-sizing:border-box}
  html,body{width:1200px;height:894px;overflow:hidden;background:var(--white)}
  body{position:relative;font-family:"Lato",sans-serif;color:var(--ink)}
  .scene{position:absolute;left:0;top:0}
  .abs{position:absolute;white-space:nowrap}

  /* header */
  .brand{left:52px;top:50px;font-size:32px;font-weight:700;color:var(--navy);line-height:1}
  .main-nav a{position:absolute;top:98px;font-size:17px;color:var(--ink);text-decoration:none}
  .main-nav a.is-active{color:var(--navy)}
  .header-phone{left:1033px;top:29px;font-size:17px;font-weight:700;color:var(--ink);letter-spacing:.3px}

  /* hero */
  .hero-title{right:53px;top:304px;text-align:right;font-family:"Cabin",sans-serif;font-weight:500;
    font-size:34px;line-height:45px;letter-spacing:-.7px;color:var(--ink)}

  /* footer */
  .footer-nav a{position:absolute;top:762px;font-size:15px;color:var(--white);text-decoration:none}
  .contact-label{font-size:15px;font-weight:700;color:var(--white)}
  .contact-value{font-size:16px;color:var(--white);margin-top:6px}
  .contact-value.email{letter-spacing:.4px}
  .copyright{right:53px;top:833px;text-align:right;font-size:14px;line-height:20px;color:var(--white)}
</style>
</head>
<body>

<svg class="scene" width="1200" height="894" viewBox="0 0 1200 894">
  <defs>
    <linearGradient id="photoTone" x1="0" y1="0" x2="1" y2="0">
      <stop offset="0" stop-color="#e6e8ec"/>
      <stop offset="0.18" stop-color="#ddd6cf"/>
      <stop offset="0.33" stop-color="#c9ad93"/>
      <stop offset="0.45" stop-color="#dcbcb8"/>
      <stop offset="0.58" stop-color="#e2d4d6"/>
      <stop offset="0.72" stop-color="#eceef5"/>
      <stop offset="1" stop-color="#eef1f9"/>
    </linearGradient>
  </defs>

  <rect class="footer-bg" x="0" y="540" width="1200" height="354" fill="var(--navy)"/>

  <line x1="0" y1="142.5" x2="1200" y2="142.5" stroke="var(--rule)"/>

  <path class="hero-photo" role="img" aria-label="Photograph of a woman in a pink sweater holding her chest, struggling to breathe, in a bright room"
        d="M0,143 H1200 V574 Q600,841 0,623 Z" fill="url(#photoTone)"/>
  <path class="hero-band" d="M0,623 Q600,841 1200,574 L1200,619 Q600,863 0,623 Z" fill="var(--sky)"/>
  <path class="hero-edge" d="M0,623 Q600,841 1200,574" fill="none" stroke="var(--white)" stroke-width="3"/>

  <g class="slider-dots">
    <circle cx="1065" cy="510" r="7" fill="var(--navy)"/>
    <circle cx="1090" cy="510" r="7" fill="var(--dot)"/>
    <circle cx="1116" cy="510" r="7" fill="var(--dot)"/>
    <circle cx="1141" cy="510" r="7" fill="var(--dot)"/>
  </g>

  <g class="header-social">
    <g fill="var(--sky-soft)" stroke="var(--sky)" stroke-width="1.5">
      <circle cx="827" cy="39" r="16.5"/>
      <circle cx="874" cy="39" r="16.5"/>
      <circle cx="921" cy="39" r="16.5"/>
    </g>
    <g fill="var(--sky)">
      <circle cx="827" cy="39" r="5"/>
      <circle cx="874" cy="39" r="5"/>
      <circle cx="921" cy="39" r="5"/>
    </g>
  </g>
  <line x1="964" y1="23" x2="964" y2="56" stroke="var(--rule)"/>

  <g class="icon-phone" transform="translate(1007 40)">
    <circle r="16" fill="none" stroke="var(--sky)" stroke-width="2"/>
    <path d="M-6,-8 l4,-1 l2,5 l-3,2 q2,5 6,7 l2,-3 l5,2 l-1,4 q-10,1 -15,-16 z" fill="var(--sky)"/>
  </g>

  <g stroke="var(--rule)">
    <line x1="540" y1="100" x2="540" y2="119"/>
    <line x1="665" y1="100" x2="665" y2="119"/>
    <line x1="797" y1="100" x2="797" y2="119"/>
    <line x1="916" y1="100" x2="916" y2="119"/>
    <line x1="1037" y1="100" x2="1037" y2="119"/>
  </g>
  <path class="nav-marker" d="M476,81 q17,17 35,0 q-17,11 -35,0z" fill="#c9d7ea"/>

  <g stroke="rgba(255,255,255,.45)">
    <line x1="117" y1="762" x2="117" y2="780"/>
    <line x1="227" y1="762" x2="227" y2="780"/>
    <line x1="348" y1="762" x2="348" y2="780"/>
    <line x1="454" y1="762" x2="454" y2="780"/>
    <line x1="562" y1="762" x2="562" y2="780"/>
  </g>

  <g class="footer-social">
    <g fill="rgba(255,255,255,.08)" stroke="var(--white)" stroke-width="1.5">
      <circle cx="1039" cy="766" r="16.5"/>
      <circle cx="1086" cy="766" r="16.5"/>
      <circle cx="1133" cy="766" r="16.5"/>
    </g>
    <g fill="var(--white)">
      <circle cx="1039" cy="766" r="5"/>
      <circle cx="1086" cy="766" r="5"/>
      <circle cx="1133" cy="766" r="5"/>
    </g>
  </g>

  <line x1="0" y1="805.5" x2="1200" y2="805.5" stroke="rgba(142,174,214,.6)"/>

  <g class="icon-pin" transform="translate(70 848)">
    <circle r="17" fill="var(--sky)"/>
    <path d="M0,8 C-4,2 -6,-1 -6,-3 A6,6 0 1 1 6,-3 C6,-1 4,2 0,8 Z" fill="var(--white)"/>
    <circle cy="-3" r="2.2" fill="var(--sky)"/>
  </g>
  <g class="icon-phone" transform="translate(417 848)">
    <circle r="17" fill="var(--sky)"/>
    <path d="M-6,-8 l4,-1 l2,5 l-3,2 q2,5 6,7 l2,-3 l5,2 l-1,4 q-10,1 -15,-16 z" fill="var(--white)"/>
  </g>
  <g class="icon-mail" transform="translate(606 848)">
    <circle r="17" fill="var(--sky)"/>
    <rect x="-8" y="-5.5" width="16" height="11" fill="var(--white)"/>
    <path d="M-8,-5.5 L0,1 L8,-5.5" fill="none" stroke="var(--sky)" stroke-width="1.3"/>
  </g>
</svg>

<header class="site-header">
  <div class="abs brand">Restwell Clinic</div>
  <nav class="main-nav">
    <a class="is-active" href="#" style="left:469px">Home</a>
    <a href="#" style="left:565px">Diagnosis</a>
    <a href="#" style="left:690px">Treatment</a>
    <a href="#" style="left:822px">Products</a>
    <a href="#" style="left:941px">About Us</a>
    <a href="#" style="left:1062px">Contact Us</a>
  </nav>
  <div class="abs header-phone">020-555-0148</div>
</header>

<section class="hero">
  <h1 class="abs hero-title">We Provide Diagnostic and Treatment<br>Solutions For Snoring, Sleep Disorders<br>And Other Respiratory Problems</h1>
</section>

<footer class="site-footer">
  <nav class="footer-nav">
    <a href="#" style="left:53px">Home</a>
    <a href="#" style="left:140px">Diagnosis</a>
    <a href="#" style="left:250px">Treatment</a>
    <a href="#" style="left:368px">Products</a>
    <a href="#" style="left:475px">About Us</a>
    <a href="#" style="left:585px">Contact Us</a>
  </nav>
  <div class="abs contact-item" style="left:98px;top:830px">
    <div class="contact-label">Restwell Clinic</div>
    <div class="contact-value">48 Harbour Lane, Eastvale - 204518</div>
  </div>
  <div class="abs contact-item" style="left:445px;top:830px">
    <div class="contact-label">Call Us :</div>
    <div class="contact-value">020-555-0148</div>
  </div>
  <div class="abs contact-item" style="left:635px;top:830px">
    <div class="contact-label">Email Us :</div>
    <div class="contact-value email">info@restwellclinic.com</div>
  </div>
  <div class="abs copyright">© 2017 Restwell Clinic.<br>All Rights Reserved.&nbsp;&nbsp;</div>
</footer>

</body>
</html>
```